Redgum Ridge Towing website

We need a website design for a towing company based in Australia.
The design should be simple and minimalist. The site can be in colours of the logo are Blue, Red and White (see attached) - but we'd like to see options in some sort of industrial looking metallic theme if possible.
We base our business on our friendly and efficient customer service, the design should attempt to convey this in some way.

```html
<!DOCTYPE html>
<html lang="en">
<head>
<meta charset="utf-8">
<title>Redgum Ridge Towing</title>
<link href="https://fonts.googleapis.com/css2?family=Open+Sans:wght@300;400;600;700&display=swap" rel="stylesheet">
<style>
:root{
  --red:#e1060c;
  --red-dark:#b90008;
  --blue:#0a5aa8;
  --blue-deep:#062f78;
  --navy:#143a78;
  --text:#555;
  --muted:#888;
  --line:#cfcfcf;
  --panel:#f2f2f2;
  --footer:#efefef;
  --white:#fff;
}
*{box-sizing:border-box;margin:0;padding:0}
html,body{width:1014px;height:1200px;overflow:hidden;background:var(--white)}
body{font-family:"Open Sans",Arial,sans-serif;color:var(--text);position:relative}
.abs{position:absolute}

/* header */
.call{right:78px;top:44px;text-align:right}
.call-label{color:var(--red);font-size:14px;line-height:18px}
.call-number{color:var(--blue);font-size:24px;line-height:30px}

.nav{left:0;top:102px;width:1014px;height:44px;background:linear-gradient(var(--red),#d00008)}
.nav a{position:absolute;top:0;height:44px;line-height:44px;color:var(--white);font-size:14.5px;font-weight:600;text-decoration:none;text-transform:uppercase}
.nav a.active{background:var(--red-dark);padding:0 22px;left:70px}

.brand{left:432px;top:0;width:150px;height:178px;background:var(--white);border-radius:0 0 20px 20px;text-align:center;padding-top:34px;z-index:3}
.brand-mark{width:54px;height:54px;border-radius:50%;background:var(--blue);margin:0 auto 12px}
.brand-name{font-size:15px;font-weight:700;color:var(--navy);line-height:19px}

/* hero */
.hero{left:0;top:146px;width:1014px;height:393px;background:linear-gradient(160deg,#b8c9d8 0%,#d9d9d9 35%,#a33 55%,#c8ccd2 72%,#7f8d6a 100%)}
.caption{left:69px;top:139px;width:436px;height:136px;background:rgba(20,20,20,.78);padding:20px 30px;color:var(--white)}
.caption h1{font-size:28px;font-weight:600;line-height:32px}
.caption h2{font-size:21px;font-weight:600;line-height:28px}
.caption p{font-size:11px;line-height:17px;color:#ccc;margin-top:6px}
.dots{left:497px;top:374px;display:flex;gap:5px}
.dots span{width:12px;height:12px;border-radius:50%;background:rgba(255,255,255,.45)}
.dots span:first-child{background:var(--white)}

/* features */
.features{left:0;top:539px;width:1014px;height:164px;background:linear-gradient(var(--blue),var(--blue-deep))}
.feature{top:29px;width:260px}
.feature h3{font-size:21px;font-weight:400;color:var(--white);line-height:26px}
.feature p{font-size:11px;line-height:17px;color:#a9c3e6;margin-top:4px}
.more{display:block;margin-top:7px;font-size:12px;font-weight:600;color:var(--white)}
.more::after{content:"";display:inline-block;margin-left:5px;border-left:5px solid #c9d7ee;border-top:4px solid transparent;border-bottom:4px solid transparent}
.divider{top:32px;width:1px;height:98px;background:rgba(255,255,255,.18)}

/* content */
.about{left:70px;top:748px;width:286px}
.about h2{font-size:26px;font-weight:400;color:#333;line-height:34px}
.about .sub{font-size:14.5px;font-weight:300;color:#333;line-height:20px;white-space:nowrap}
.photo{width:284px;height:107px;margin:8px 0 10px;background:linear-gradient(135deg,#9aa3a8,#c9c9c4 50%,#d63b2f 80%)}
.about p{font-size:11px;line-height:19px;color:#666;margin-bottom:4px}

.services{left:391px;top:752px;width:260px}
.services h2{font-size:23px;font-weight:400;color:var(--red);line-height:30px}
.service{position:absolute;left:0;width:260px}
.thumb{position:absolute;left:0;top:0;width:102px;height:72px}
.service h4{position:absolute;left:112px;top:0;font-size:14px;font-weight:600;color:var(--navy);white-space:nowrap}
.service p{position:absolute;left:112px;top:22px;width:150px;font-size:11px;line-height:19px;color:#777}

.contact{left:675px;top:740px;width:270px;height:326px;background:var(--panel);border:1px solid #ddd}
.contact-head{height:49px;border-bottom:1px solid #ddd;padding:10px 22px;font-size:22px;font-weight:400;color:#555}
.field{position:absolute;left:18px;width:234px;height:27px;background:linear-gradient(var(--white),#eee);border:1px solid var(--line);font-size:11px;color:#666;padding:6px 11px}
.submit{position:absolute;left:18px;top:275px;width:84px;height:28px;background:var(--red);color:var(--white);font-size:13px;font-weight:700;text-align:center;line-height:28px;border-radius:2px}

/* footer */
.footer{left:0;top:1097px;width:1014px;height:103px;background:var(--footer)}
.footer-links{left:76px;top:24px;font-size:14px;color:#555;font-weight:600}
.footer-links span{color:#999;margin:0 7px;font-weight:400}
.copy{left:76px;top:53px;font-size:12px;color:#999}
.social{left:831px;top:27px;display:flex;gap:8px}
.social span{width:21px;height:21px;border-radius:2px}
</style>
</head>
<body>

<header>
  <div class="abs call">
    <div class="call-label">CALL US NOW</div>
    <div class="call-number">623-555-0148</div>
  </div>
  <nav class="abs nav">
    <a class="active" href="#">Home</a>
    <a href="#" style="left:170px">About Us</a>
    <a href="#" style="left:276px">Services</a>
    <a href="#" style="left:377px">Blog</a>
    <a href="#" style="left:593px">Support</a>
    <a href="#" style="left:694px">Testimonials</a>
    <a href="#" style="left:831px">Contact Us</a>
  </nav>
  <div class="abs brand">
    <div class="brand-mark"></div>
    <div class="brand-name">Redgum Ridge Towing</div>
  </div>
</header>

<section class="abs hero" role="img" aria-label="Red tow truck hauling a motorhome on a flatbed trailer">
  <div class="abs caption">
    <h1>PROVIDE TOWING SERVICES</h1>
    <h2>ETIAM EU URNA SED PORTA</h2>
    <p>Aliquam nec erat at purus cursus interdum Vestibulum ligula augue bibendum accumsan vestibulum ut commodo a mi Morbi orna</p>
  </div>
  <div class="abs dots"><span></span><span></span><span></span><span></span></div>
</section>

<section class="abs features">
  <div class="abs feature" style="left:92px">
    <h3>24/7 SUPPORT</h3>
    <p>Aliquam nec erat at purus cursus interdum Vestibulum ligula augue bibendum accumsan vestibulum ut commodo a mi Morbi orna</p>
    <span class="more">READ MORE</span>
  </div>
  <div class="abs divider" style="left:360px"></div>
  <div class="abs feature" style="left:384px">
    <h3>SERVICES PROVIDE</h3>
    <p>Aliquam nec erat at purus cursus interdum Vestibulum ligula augue bibendum accumsan vestibulum ut commodo a mi Morbi orna</p>
    <span class="more">READ MORE</span>
  </div>
  <div class="abs divider" style="left:651px"></div>
  <div class="abs feature" style="left:675px">
    <h3>OUR MISSION</h3>
    <p>Aliquam nec erat at purus cursus interdum Vestibulum ligula augue bibendum accumsan vestibulum ut commodo a mi Morbi orna</p>
    <span class="more">READ MORE</span>
  </div>
</section>

<section class="abs about">
  <h2>About Our Company</h2>
  <div class="sub">Mauris nunc quam venenatis nec euismod</div>
  <div class="photo" role="img" aria-label="Tow operator loading a small SUV onto a red flatbed"></div>
  <p>Etiam eu urna Sed porta Suspendisse quam leo molestie sed luctus quis feugiat in pede Fusce tellus Sed metus augue convallis et vehicula ut pulvinar eu ante Integer orci tellus tristique vitae consequat nec porta vel</p>
  <p>Phasellus felis dolor scelerisque a tempus eget lobortis id libero Aliquam nec erat at purus cursus interdum</p>
</section>

<section class="abs services">
  <h2>Towing Services</h2>
  <div class="service" style="top:40px">
    <div class="thumb" role="img" aria-label="Blue tow truck carrying a silver car" style="background:linear-gradient(#3f78c8,#2a4f8c 60%,#5c8f3a)"></div>
    <h4>Etiam eu urna Sed</h4>
    <p>Suspendisse quam leo molestie sed luctus quis feugiat in pede Fusce tellus</p>
  </div>
  <div class="service" style="top:130px">
    <div class="thumb" role="img" aria-label="Red tow truck with a car on its flatbed" style="background:linear-gradient(#9bb3c8,#c8303a 55%,#6a8a3c)"></div>
    <h4>Phasellus felis dolor</h4>
    <p>Suspendisse quam leo molestie sed luctus quis feugiat in pede Fusce tellus</p>
  </div>
  <div class="service" style="top:223px">
    <div class="thumb" role="img" aria-label="Blue heavy tow truck with flatbed" style="background:linear-gradient(#6f9ad8,#1d3f9c 55%,#6e6e6e)"></div>
    <h4>Morbi ornare gravida</h4>
    <p>Suspendisse quam leo molestie sed luctus quis feugiat in pede Fusce tellus</p>
  </div>
</section>

<aside class="abs contact">
  <div class="contact-head">Quick Contact Us</div>
  <div class="field" style="top:66px">Your Name</div>
  <div class="field" style="top:101px">Email address</div>
  <div class="field" style="top:137px">Phone no.</div>
  <div class="field" style="top:172px">Location</div>
  <div class="field" style="top:208px;height:62px">Comment / Message</div>
  <div class="submit">SUBMIT</div>
</aside>

<footer class="abs footer">
  <div class="abs footer-links">Home<span>|</span>About us<span>|</span>Services<span>|</span>Testimonials<span>|</span>Blog<span>|</span>Support<span>|</span>Contact</div>
  <div class="abs copy">Copyright © 2014 Company Name.&nbsp; All right reserved</div>
  <div class="abs social">
    <span style="background:#3b5a9a"></span>
    <span style="background:#3fa9de"></span>
    <span style="background:#1b75b5"></span>
    <span style="background:#f0892a"></span>
  </div>
</footer>

</body>
</html>
```